Buisness card design

Design 3 different cards all with the same theme. You can visit our website at meadowpawhaven.com to get a better feel for our color scheme and style, preferably a minimalistic design.
design one (grooming):
Darla Whitcomb
319-555-0182
4815 North Birch Avenue Linden Vale OR
This card must have a spot on the back to schedule the next grooming appointment. Please also include a QR code to https://www.meadowpawhaven.com/dog-grooming/ if possible.
Design two (training)
Nora Kesselworth
319-555-0147
This card is for our trainer and her training program. Please also include a QR code to https://www.meadowpawhaven.com/dog-training/
Design three (training)
Bright Hollow
Daycare, Grooming, Boarding, Training
319-555-0182
This card is just a general card that all staff can use if needed. Please also include a QR code to https://www.meadowpawhaven.com/
Industry/Entity Type
pet, dog daycare
Contact Information for Business Card
name, number, location

```html
<!DOCTYPE html>
<html lang="en">
<head>
<meta charset="utf-8">
<title>Bright Hollow – Grooming Business Card</title>
<link rel="stylesheet" href="https://fonts.googleapis.com/css2?family=Exo+2:wght@300;400&family=Michroma&family=Roboto:wght@400&display=swap">
<style>
  :root {
    --backdrop: #e4e4e4;
    --card-dark: #1b1b1b;
    --card-dark-soft: #2a2a2a;
    --card-light: #f6f6f6;
    --ink: #1a1a1a;
    --accent-blue: #3aa0f0;
    --form-blue: #2f7fe0;
    --wash-blue: #c9dbf5;
    --wash-grey: #d4d4d4;
    --footer-gold: #c8862a;
    --form-bg: #f4f4f4;
  }
  * { box-sizing: border-box; margin: 0; padding: 0; }
  html, body {
    width: 1200px; height: 1200px; overflow: hidden;
    background: var(--backdrop);
  }
  .card {
    position: absolute; left: 262px;
    width: 686px; height: 392px;
    border-radius: 18px; overflow: hidden;
  }
  /* front */
  .card--front { top: 165px; background: var(--card-dark); }
  .front-panel { position: absolute; inset: 0; }
  .front-art {
    position: absolute; left: 20px; top: 10px; width: 560px; height: 370px;
    border-radius: 50% 45% 40% 50%;
    background: radial-gradient(ellipse at 45% 55%, var(--wash-grey) 0%, rgba(201,219,245,0.55) 45%, rgba(246,246,246,0) 72%);
  }
  .contact {
    position: absolute; right: 72px; top: 28px;
    font-family: "Exo 2", sans-serif; font-weight: 300;
    font-size: 16px; line-height: 21px; color: var(--ink);
    text-align: right; list-style: none;
  }
  .contact li { position: relative; }
  .contact .icon {
    position: absolute; right: -26px; top: 4px; width: 13px; height: 13px;
  }
  .holder-name {
    position: absolute; right: 38px; top: 320px;
    font-family: "Michroma", sans-serif; font-size: 24px;
    letter-spacing: 1px; color: #000; text-transform: uppercase;
    font-weight: 400; -webkit-text-stroke: 0.8px #000;
  }
  /* back */
  .card--back {
    top: 653px;
    background: linear-gradient(135deg, var(--card-dark) 0%, #141414 45%, var(--card-dark-soft) 100%);
  }
  .brand {
    position: absolute; left: 0; right: 0; top: 150px;
    display: flex; align-items: center; justify-content: center; gap: 12px;
    font-family: "Exo 2", sans-serif; font-weight: 400;
    font-size: 30px; line-height: 36px; color: #f2f2f2; letter-spacing: 1px;
  }
  .brand-dot { width: 14px; height: 14px; border-radius: 50%; background: #f2f2f2; }
  .appointment {
    position: absolute; left: 41px; top: 232px; width: 604px; height: 93px;
    background: var(--form-bg); border-radius: 14px;
    padding: 14px 28px 0 24px;
    font-family: "Roboto", sans-serif; font-size: 16px; color: var(--form-blue);
  }
  .field-row { display: flex; align-items: baseline; height: 36px; line-height: 28px; }
  .field-label { white-space: nowrap; }
  .field-line {
    display: inline-block; flex: 1; margin: 0 4px 0 6px;
    height: 1px; border-bottom: 1px dotted #555;
  }
  .field-line--short { flex: 1.5; }
  .web-link {
    position: absolute; left: 0; right: 0; top: 348px; text-align: center;
    font-family: "Exo 2", sans-serif; font-size: 15px;
    letter-spacing: 4px; color: var(--footer-gold);
  }
</style>
</head>
<body>

<section class="card card--front">
  <svg class="front-panel" viewBox="0 0 686 392" width="686" height="392" aria-hidden="true">
    <path d="M205 0 H686 V392 H140 C60 370 10 320 12 240 C14 150 110 40 205 0 Z" fill="var(--card-light)"/>
    <path d="M205 0 C110 40 14 150 12 240 C10 320 60 370 140 388 L686 384" fill="none" stroke="var(--wash-blue)" stroke-width="5"/>
  </svg>
  <div class="front-art" role="img" aria-label="Line illustration of a dog being washed under a shower head with soap bubbles"></div>

  <ul class="contact">
    <li>319-555-0182
      <svg class="icon" viewBox="0 0 24 24" aria-hidden="true"><path fill="var(--accent-blue)" d="M6.6 10.8a15.1 15.1 0 0 0 6.6 6.6l2.2-2.2c.3-.3.7-.4 1-.2 1.1.4 2.3.6 3.6.6.6 0 1 .4 1 1V20c0 .6-.4 1-1 1A17 17 0 0 1 3 4c0-.6.4-1 1-1h3.5c.6 0 1 .4 1 1 0 1.3.2 2.5.6 3.6.1.3 0 .7-.2 1z"/></svg>
    </li>
    <li>meadowpawhaven.com
      <svg class="icon" viewBox="0 0 24 24" aria-hidden="true"><circle cx="12" cy="12" r="10" fill="var(--accent-blue)"/><path d="M2 12h20M12 2c3 3 3 17 0 20M12 2c-3 3-3 17 0 20" stroke="#fff" stroke-width="1.4" fill="none"/></svg>
    </li>
    <li>4815 North Birch Avenue
      <svg class="icon" viewBox="0 0 24 24" aria-hidden="true"><path fill="var(--accent-blue)" d="M12 2a7 7 0 0 0-7 7c0 5 7 13 7 13s7-8 7-13a7 7 0 0 0-7-7zm0 9.5A2.5 2.5 0 1 1 12 6.5a2.5 2.5 0 0 1 0 5z"/></svg>
    </li>
    <li>Linden Vale OR</li>
  </ul>

  <h1 class="holder-name">Darla Whitcomb</h1>
</section>

<section class="card card--back">
  <div class="brand"><span class="brand-dot"></span>Bright Hollow</div>

  <div class="appointment">
    <div class="field-row">
      <span class="field-label">NAME</span><span class="field-line"></span>
    </div>
    <div class="field-row">
      <span class="field-label">DATE</span><span class="field-line field-line--short"></span>
      <span class="field-label">TIME</span><span class="field-line"></span>
      <span class="field-label">AM/PM</span>
    </div>
  </div>

  <p class="web-link">www.meadowpawhaven.com/dog-grooming</p>
</section>

</body>
</html>
```